Heron Loan Partners Business Card

We need a business card design for our mortgage servicing company. In addition to servicing the loans of homeowners, we help homeowners with purchasing their homes and any mortgage refinancing. We would like to see designs that use the colors in the logo attached below (gold-ish yellow and navy blue), and any other design you deem fit! The design should communicate a simpler life with smart mortgages provided by Heron.

```html
<!DOCTYPE html>
<html lang="en">
<head>
<meta charset="utf-8">
<title>Heron Loan Partners – Business Card</title>
<link href="https://fonts.googleapis.com/css2?family=Raleway:wght@400;700&family=Open+Sans:wght@400&display=swap" rel="stylesheet">
<style>
  :root {
    --backdrop: #559bb5;
    --card: #ffffff;
    --navy: #25204f;
    --gold: #e2ae3b;
  }
  * { box-sizing: border-box; margin: 0; padding: 0; }
  html, body { width: 1008px; height: 1200px; overflow: hidden; }
  body { background: var(--backdrop); position: relative; font-family: "Open Sans", sans-serif; color: var(--navy); }

  .card {
    position: absolute; left: 115px; width: 777px; height: 444px;
    background: var(--card);
    box-shadow: 8px 10px 14px rgba(20, 50, 70, 0.35);
  }
  .card--front { top: 122px; }
  .card--back { top: 626px; }

  .brand {
    position: absolute; left: 0; right: 0;
    display: flex; align-items: center; justify-content: center; gap: 12px;
  }
  .card--front .brand { top: 96px; }
  .card--back .brand { top: 210px; }
  .brand__dot { width: 22px; height: 22px; border-radius: 50%; background: var(--gold); }
  .brand__name {
    font-family: "Raleway", sans-serif; font-weight: 700; font-size: 34px;
    color: var(--navy); letter-spacing: 0.5px;
  }

  .person { position: absolute; left: 41px; top: 268px; font-family: "Raleway", sans-serif; }
  .person__name { font-size: 27px; line-height: 1; letter-spacing: -0.3px; font-weight: 400; }
  .person__name strong { font-weight: 700; }
  .person__title { font-size: 20px; margin-top: 6px; font-weight: 400; }

  .rule { position: absolute; left: 0; width: 777px; height: 18px; }
  .rule polygon, .rule .rule__navy { fill: var(--navy); }
  .rule .rule__gold { fill: var(--gold); }

  .contacts { position: absolute; top: 377px; left: 0; width: 777px; height: 36px; }
  .contact { position: absolute; top: 0; display: flex; align-items: center; gap: 10px; }
  .contact__icon {
    width: 35px; height: 35px; border-radius: 50%; background: var(--navy);
    display: flex; align-items: center; justify-content: center; flex: none;
  }
  .contact__icon svg { width: 20px; height: 20px; fill: #fff; }
  .contact__text { font-size: 15.5px; line-height: 19px; white-space: nowrap; }
  .contact--address { left: 39px; }
  .contact--web { left: 279px; }
  .contact--phone { left: 543px; }
</style>
</head>
<body>

  <section class="card card--front">
    <div class="brand">
      <span class="brand__dot"></span>
      <span class="brand__name">Heron Loan Partners</span>
    </div>

    <div class="person">
      <h1 class="person__name"><strong>DANIEL</strong>WHITMORE</h1>
      <p class="person__title">Managing Director</p>
    </div>

    <svg class="rule" style="top:328px" viewBox="0 0 777 18">
      <rect class="rule__gold" x="369" y="6" width="369" height="6"/>
      <polygon points="38,0 362,0 376,18 38,18"/>
    </svg>

    <div class="contacts">
      <div class="contact contact--address">
        <span class="contact__icon">
          <svg viewBox="0 0 24 24"><path d="M12 3 2 12h3v8h5v-5h4v5h5v-8h3z"/></svg>
        </span>
        <p class="contact__text">Street Address Here<br>Street Address Here</p>
      </div>
      <div class="contact contact--web">
        <span class="contact__icon">
          <svg viewBox="0 0 24 24"><path d="M3 4l18 7-8 2-3 8z"/></svg>
        </span>
        <p class="contact__text">hello@heronloans.com<br>www.heronloans.com</p>
      </div>
      <div class="contact contact--phone">
        <span class="contact__icon">
          <svg viewBox="0 0 24 24"><path d="M3 9c0-3 4-5 9-5s9 2 9 5v2h-5V9H8v2H3zM6 12h12l2 8H4zm6 2a2.5 2.5 0 1 0 0 5 2.5 2.5 0 0 0 0-5z"/></svg>
        </span>
        <p class="contact__text">+18 2555 0140 1200<br>+18 2555 0140 1200</p>
      </div>
    </div>
  </section>

  <section class="card card--back">
    <svg class="rule" style="top:53px" viewBox="0 0 777 18">
      <rect class="rule__gold" x="369" y="6" width="369" height="6"/>
      <polygon points="38,0 362,0 376,18 38,18"/>
    </svg>

    <div class="brand">
      <span class="brand__dot"></span>
      <span class="brand__name">Heron Loan Partners</span>
    </div>

    <svg class="rule" style="top:377px" viewBox="0 0 777 18">
      <rect class="rule__gold" x="38" y="6" width="370" height="6"/>
      <polygon points="413,0 738,0 738,18 400,18"/>
    </svg>
  </section>

</body>
</html>
```